Comprehensive and creative superhero design needed for our mortgage company

We are a mortgage company called Brightfall Mortgages, and we are looking for a mascot to help project our identity. Our goal is to create a mascot that can express an explosive yet professional image. More importantly, we want our mascot to be universal and welcoming to people of all backgrounds. Our target audience is new and upcoming homebuyers.

We're looking for a mascot similar to "Don Vireno" from the old Plimsa commercials. We would like to include some form of a mask, and we don't mind the buff yet short physique of the character to remain the same. However, his character build and wardrobe is completely up to your interpretation, we are open to new ideas. It is important to note that we work with homes and money. Our two main colours are purple and yellow, however we are open to trying different colours such as green or blue. We embrace the concept that less is more.

Our plan is to display the mascot on the many trucks that we own to be advertised around the area, and we would like to include him on various other forms of media as well (website, social media, etc.). It is important to remember that the design we choose will be blown up to a much larger size. The most important part of our mascot project is that we need him in several poses so that we can incorporate him into our designs effectively. We've attached a file with the poses we would like to see the character in. These poses can either be included in your initial design, or they can be made after your design if it has been chosen. We also attached a file of "Don Vireno," and we included the potential design of our truck for inspiration.

Note: The design must be different enough to avoid any copyright issues with the "Don Vireno" design from Plimsa

We look forward to seeing your designs! :)

```html
<!DOCTYPE html>
<html lang="en">
<head>
<meta charset="utf-8">
<title>Brightfall Mortgages – Trailer Wraps</title>
<link rel="stylesheet" href="https://fonts.googleapis.com/css2?family=Anton&family=Luckiest+Guy&display=swap">
<style>
  :root {
    --purple: #92368f;
    --purple-deep: #6e2470;
    --yellow: #fdcc07;
    --warm: #f2b98a;
    --white: #ffffff;
    --edge: #1a1a1a;
    --page: #ffffff;
  }
  * { box-sizing: border-box; margin: 0; padding: 0; }
  html, body { width: 1200px; height: 583px; overflow: hidden; background: var(--page); }
  .canvas { position: relative; width: 1200px; height: 583px; }

  .wrap {
    position: absolute;
    background: var(--purple);
    border: 2px solid var(--edge);
    overflow: hidden;
  }
  .wrap--side-a { left: 283px; top: 58px;  width: 620px; height: 158px; }
  .wrap--side-b { left: 285px; top: 330px; width: 618px; height: 155px; }
  .wrap--rear-a { left: 992px; top: 51px;  width: 168px; height: 182px; }
  .wrap--rear-b { left: 993px; top: 324px; width: 167px; height: 183px; }

  .burst { position: absolute; left: 0; top: 0; width: 100%; height: 100%; }
  .burst polygon { fill: var(--yellow); }

  .mascot {
    position: absolute;
    border-radius: 45% 45% 30% 30%;
    background: radial-gradient(ellipse at 50% 30%, var(--warm) 0%, var(--yellow) 45%, var(--purple-deep) 100%);
  }

  .wordmark {
    position: absolute;
    font-family: "Anton", sans-serif;
    font-weight: 400;
    color: var(--white);
    line-height: 0.95;
    white-space: nowrap;
  }
  .wordmark__web { font-size: 0.32em; }
  .wordmark__line { display: block; }

  .slogan {
    position: absolute;
    font-family: "Luckiest Guy", "Anton", sans-serif;
    font-weight: 400;
    color: var(--purple);
    line-height: 1;
    white-space: nowrap;
    text-align: center;
    letter-spacing: 0.02em;
  }
</style>
</head>
<body>
<main class="canvas">

  <section class="wrap wrap--side-a">
    <svg class="burst" viewBox="0 0 620 158" preserveAspectRatio="none" aria-hidden="true">
      <polygon points="230,20 300,30 320,0 520,0 510,25 555,65 520,80 550,120 490,125 480,158 260,158 275,135 245,115 265,95 200,88 270,60"/>
    </svg>
    <div class="mascot" role="img" aria-label="Brand mascot illustration" style="left:84px;top:6px;width:92px;height:146px;"></div>
    <div class="wordmark" style="left:258px;top:20px;font-size:50px;">
      <span class="wordmark__line"><span class="wordmark__web">www.</span>Brightfall</span>
      <span class="wordmark__line" style="font-size:42px;">Mortgages.ca</span>
    </div>
    <div class="slogan" style="left:314px;top:120px;width:140px;font-size:16px;">WE CAN HELP</div>
  </section>

  <section class="wrap wrap--side-b">
    <svg class="burst" viewBox="0 0 618 155" preserveAspectRatio="none" aria-hidden="true">
      <polygon points="400,55 440,28 490,48 500,25 520,45 560,40 545,70 575,80 545,95 570,115 535,125 520,135 480,130 460,145 440,130 405,135 415,110 385,92 410,82"/>
    </svg>
    <div class="wordmark" style="left:28px;top:22px;font-size:58px;">
      <span class="wordmark__line"><span class="wordmark__web">www.</span>Brightfall</span>
      <span class="wordmark__line" style="font-size:52px;">Mortgages.ca</span>
    </div>
    <div class="slogan" style="left:428px;top:60px;width:110px;font-size:22px;">WE CAN<br><span style="font-size:32px;">HELP</span></div>
  </section>

  <section class="wrap wrap--rear-a">
    <svg class="burst" viewBox="0 0 168 182" preserveAspectRatio="none" aria-hidden="true">
      <polygon points="60,15 75,0 168,0 168,45 140,50 125,60 110,50 90,55 95,38 55,30 75,22"/>
    </svg>
    <div class="slogan" style="left:68px;top:13px;width:96px;font-size:5.5px;">MORTGAGES AREN'T EASY.<br><span style="font-size:7.5px;">WE'RE HERE TO HELP</span></div>
    <div class="mascot" role="img" aria-label="Brand mascot illustration" style="left:12px;top:32px;width:100px;height:88px;"></div>
    <div class="wordmark" style="left:14px;top:124px;font-size:23px;">
      <span class="wordmark__line"><span class="wordmark__web">www.</span>Brightfall</span>
      <span class="wordmark__line" style="font-size:21px;">Mortgages.ca</span>
    </div>
  </section>

  <section class="wrap wrap--rear-b">
    <div class="wordmark" style="left:14px;top:18px;font-size:23px;">
      <span class="wordmark__line"><span class="wordmark__web">www.</span>Brightfall</span>
      <span class="wordmark__line" style="font-size:21px;">Mortgages.ca</span>
    </div>
    <div class="mascot" role="img" aria-label="Brand mascot illustration" style="left:38px;top:74px;width:100px;height:104px;"></div>
  </section>

</main>
</body>
</html>
```